Heron Haulage needs Bussiness cards!

Our new trucking company needs business cards!
We need the same design with two different names and emails, everything else it's the same.
I have included our original logo so we can use it for the design.
Note: the logo to be used is the o e with the buffalo on the right side, next to the letters H and H.

Target Market(s)

Trucking, refrigerated transportation, freight

Industry/Entity Type

Business

Contact Information for Business Card

Card #1:
Marcus Whitfield
marcuswhitfield@heronhaulage.example
1-855-317-6094
(956)238-7160
4117 W. Larkin Ave.
Pharr, TX 78590
www.heronhaulage.example

Card#2:
Rosalba Quintero
rosalba@heronhaulage.example
1-855-317-6094
(956)238-7160
4117 W. Larkin Ave.
Pharr, TX 78590
www.heronhaulage.example

Font styles to use
Sans Serif

Colors
0655a3
ec1f27
ffffff

Requirements
Must have
• our logo
Nice to have
• roads on background,

```html
<!DOCTYPE html>
<html lang="en">
<head>
<meta charset="utf-8">
<title>Heron Haulage – Business Card</title>
<link href="https://fonts.googleapis.com/css2?family=Roboto:wght@300;400;900&display=swap" rel="stylesheet">
<style>
  :root{
    --brand-navy:#0655a3;
    --brand-red:#ec1f27;
    --brand-sky:#1a9ad6;
    --brand-deep:#0b3f7c;
    --paper:#ffffff;
    --ink-grey:#6b6b6b;
    --backdrop:#e6e7e9;
  }
  *{box-sizing:border-box;margin:0;padding:0}
  html,body{width:1200px;height:950px;overflow:hidden}
  body{
    background:var(--backdrop);
    font-family:"Roboto",sans-serif;
    display:flex;flex-direction:column;align-items:center;
    justify-content:center;gap:50px;
  }
  .card{
    position:relative;width:700px;height:400px;overflow:hidden;
    box-shadow:0 4px 14px rgba(0,0,0,.18);
  }

  /* Front side */
  .card--front{background:var(--paper);display:flex;flex-direction:column;align-items:center;justify-content:center}
  .wordmark{display:flex;align-items:center;gap:14px}
  .wordmark__dot{width:22px;height:22px;border-radius:50%;background:var(--brand-red)}
  .wordmark__name{font-weight:900;font-size:58px;letter-spacing:-1px;color:var(--brand-navy);line-height:1}
  .card--front .website{margin-top:58px;font-size:15px;font-weight:400;letter-spacing:6px;color:var(--ink-grey)}

  /* Back side */
  .card--back{background:var(--brand-sky);color:var(--paper)}
  .red-band{position:absolute;right:0;top:0;width:120px;height:100%;background:var(--brand-red);
    clip-path:polygon(45% 0,100% 0,100% 100%,0 100%)}
  .mascot-area{position:absolute;right:70px;top:0;width:250px;height:100%;
    background:linear-gradient(160deg,var(--brand-navy),var(--brand-deep));
    clip-path:polygon(20% 0,100% 0,100% 100%,0 100%)}
  .back-content{position:absolute;left:48px;top:70px}
  .card--back .wordmark__name{font-size:34px;color:var(--paper)}
  .card--back .wordmark__dot{width:14px;height:14px;background:var(--brand-red)}
  .card--back .wordmark{gap:10px}
  .person{margin-top:26px;font-size:24px;font-weight:400}
  .address{margin-top:8px;font-size:14px;font-weight:300;line-height:1.35}
  .contacts{list-style:none;margin-top:18px;font-size:14px;font-weight:300}
  .contacts li{display:flex;align-items:center;gap:10px;line-height:1.55}
  .contacts svg{width:14px;height:14px;flex:none}
</style>
</head>
<body>
  <section class="card card--front" aria-label="Card front">
    <div class="wordmark">
      <span class="wordmark__dot"></span>
      <span class="wordmark__name">Heron Haulage</span>
    </div>
    <p class="website">www.heronhaulage.example</p>
  </section>

  <section class="card card--back" aria-label="Card back">
    <div class="mascot-area" role="img" aria-label="Large brand mascot illustration in navy and blue"></div>
    <div class="red-band"></div>
    <div class="back-content">
      <div class="wordmark">
        <span class="wordmark__dot"></span>
        <span class="wordmark__name">Heron Haulage</span>
      </div>
      <p class="person">Marcus Whitfield</p>
      <p class="address">4117 W. Larkin Ave.<br>Pharr, TX 78590</p>
      <ul class="contacts">
        <li>
          <svg viewBox="0 0 16 16" aria-hidden="true"><path fill="#fff" d="M3 1l3 3-1.5 2a9 9 0 0 0 5.5 5.5L12 10l3 3-2 2C7 15 1 9 1 3z"/></svg>
          1-855-317-6094
        </li>
        <li>
          <svg viewBox="0 0 16 16" aria-hidden="true"><rect x="4" y="1" width="8" height="14" rx="1.5" fill="none" stroke="#fff" stroke-width="1.5"/><circle cx="8" cy="12.5" r="1" fill="#fff"/></svg>
          (956)238-7160
        </li>
        <li>
          <svg viewBox="0 0 16 16" aria-hidden="true"><rect x="1" y="3" width="14" height="10" rx="1" fill="#fff"/><path d="M1.5 3.5L8 9l6.5-5.5" fill="none" stroke="var(--brand-sky)" stroke-width="1.3"/></svg>
          marcuswhitfield@heronhaulage.example
        </li>
        <li>
          <svg viewBox="0 0 16 16" aria-hidden="true"><circle cx="8" cy="8" r="6.5" fill="none" stroke="#fff" stroke-width="1.5"/><path d="M1.5 8h13M8 1.5c-3 3.5-3 9.5 0 13M8 1.5c3 3.5 3 9.5 0 13" fill="none" stroke="#fff" stroke-width="1.2"/></svg>
          www.heronhaulage.example
        </li>
      </ul>
    </div>
  </section>
</body>
</html>
```